Long webpage to explain and sell a complex concept

Accountancy firm wishes to explain Management Accounting to a Small Business audience. We have written the text, assembled a couple of charts and quotes and some concept photos.
There is a lot of text and it is required to explain this type of accounting.
Rather than have a long single block of text which is less likely to be read, we want to break it up with pictures, appropriate white space, diagrams etc. Someone landing on this page will then scroll down reading the text which is designed to keep you reading more.
The page on the website where this will go is https://www.brindlequay.com.au/services/management-accountants-perth/
So the fonts/colours need to fit in. Notice there is a pallet of colours which can be seen here: https://www.brindlequay.com.au/services/

Target Market(s)

Small Business owners in Perth, Western Australia

Number of Pages Required

1 page

Requirements
Must have
• The look and feel needs to match the website indicated in the description above. However we're happy to make the design of this page more interesting than the rest of the site.

```html
<!DOCTYPE html>
<html lang="en">
<head>
<meta charset="utf-8">
<title>Services – Brindle Quay</title>
<link href="https://fonts.googleapis.com/css2?family=Fira+Sans:wght@400;500;600;700&family=Lato:wght@400;700&family=Arimo:wght@400;700&display=swap" rel="stylesheet">
<style>
:root{
  --navy:#2b5a80;
  --navy-dark:#234a6a;
  --ink:#3a3a3a;
  --muted:#555;
  --sky:#3aa9ee;
  --coral:#e15b62;
  --grey-band:#e8e8e8;
  --teal:#168ab2;
  --footer:#2c4f70;
  --purple:#8a2378;
  --link:#2e8fd6;
  --white:#fff;
}
*{box-sizing:border-box;margin:0;padding:0}
html,body{width:1200px;height:4062px;overflow:hidden}
body{position:relative;background:var(--white);font-family:"Lato",sans-serif;color:var(--ink)}
.abs{position:absolute}

/* top bar */
.topbar{left:0;top:0;width:1200px;height:41px;background:var(--navy);color:var(--white);font-family:"Lato",sans-serif;font-size:15px}
.topbar .contact{position:absolute;left:143px;top:11px;display:flex;gap:34px}
.topbar .contact span{display:flex;align-items:center;gap:8px}
.topbar .social{position:absolute;right:143px;top:11px;display:flex;gap:22px;font-weight:700;font-size:14px}

/* header */
.header{left:0;top:41px;width:1200px;height:103px;background:var(--white)}
.brand{position:absolute;left:143px;top:18px}
.brand .name{font-family:"Fira Sans",sans-serif;font-weight:600;font-size:38px;color:var(--navy);letter-spacing:-1px;line-height:1}
.brand .tag{font-family:"Arimo",sans-serif;font-size:11.5px;color:var(--navy);margin:6px 0 0 46px}
.btn-consult{position:absolute;left:864px;top:24px;width:192px;height:33px;background:var(--navy);color:var(--white);font-family:"Arimo",sans-serif;font-size:14px;display:flex;align-items:center;justify-content:center;border-radius:2px}
.nav{position:absolute;right:144px;top:66px;display:flex;gap:33px;font-family:"Arimo",sans-serif;font-size:13px;color:#333}
.nav .active{color:var(--navy)}

/* hero */
.hero{left:0;top:144px;width:1200px;height:400px;background:linear-gradient(100deg,#4a5560 0%,#6c7680 35%,#5d6670 65%,#3e4852 100%)}
.hero h1{position:absolute;left:0;right:0;top:152px;text-align:center;font-family:"Fira Sans",sans-serif;font-weight:700;font-size:78px;color:var(--white);letter-spacing:1px}

/* intro */
.intro{left:143px;top:614px;width:914px;text-align:center;font-size:16.5px;line-height:32px;color:var(--muted)}
.intro p{margin-bottom:32px}
.video{left:143px;top:1033px;width:913px;height:448px;background:linear-gradient(180deg,#4b5660 0%,#3b4650 50%,#5a5248 100%)}
.video .play{position:absolute;left:428px;top:195px}
.quote{left:143px;top:1527px;width:914px;text-align:center;font-size:16.5px;line-height:32px;color:var(--muted)}
.quote p{margin-bottom:32px}
.quote .cta-line{font-size:16px;color:#333}
.quote .cta-line .c{color:var(--purple)}
.quote .cta-line .r{color:var(--link)}

/* accordion */
.band{left:0;top:1867px;width:1200px;height:1189px;background:var(--grey-band)}
.acc{position:absolute;left:143px;width:913px}
.acc-head{height:50px;display:flex;align-items:center;justify-content:space-between;padding:0 22px;color:var(--white);font-family:"Fira Sans",sans-serif;font-weight:500;font-size:23px;background:var(--sky)}
.acc-head.open{background:var(--coral)}
.acc-head svg{flex:none}
.acc-body{background:var(--white);height:364px;position:relative}
.acc-body .text{position:absolute;left:22px;top:22px;width:560px;font-size:12.6px;line-height:24px;color:#333}
.acc-body .text p{margin-bottom:24px}
.acc-body .photo{position:absolute;left:606px;top:30px;width:290px;height:298px;background:linear-gradient(135deg,#cfe0d4,#e9efe8 50%,#a9c3b2)}

/* contact form */
.form-title{left:0;top:3136px;width:1200px;text-align:center;font-family:"Fira Sans",sans-serif;font-weight:600;font-size:32px;color:#222}
.field{position:absolute;top:3193px;height:38px;width:218px;border:1px solid #bdbdbd;font-size:11.5px;color:#777;padding:13px 15px}
.field.msg{left:143px;top:3249px;width:913px;height:110px}
.submit{left:544px;top:3378px;width:112px;height:40px;background:var(--navy);color:var(--white);font-family:"Fira Sans",sans-serif;font-size:19px;display:flex;align-items:center;justify-content:center;border-radius:2px}

/* cta band */
.cta{left:0;top:3509px;width:1200px;height:121px;background:var(--teal)}
.cta p{position:absolute;left:63px;top:33px;font-family:"Arimo",sans-serif;font-size:24px;line-height:32px;color:var(--white)}
.cta .btn{position:absolute;left:935px;top:37px;width:202px;height:45px;background:var(--white);color:var(--navy-dark);font-family:"Arimo",sans-serif;font-size:15px;display:flex;align-items:center;justify-content:center;border-radius:4px}

/* footer */
.footer{left:0;top:3630px;width:1200px;height:432px;background:linear-gradient(180deg,#2f5576,#2a4a68);color:var(--white)}
.footer .brand-f{position:absolute;left:68px;top:58px}
.footer .brand-f .name{font-family:"Fira Sans",sans-serif;font-weight:600;font-size:33px;letter-spacing:-1px;line-height:1}
.footer .brand-f .tag{font-family:"Arimo",sans-serif;font-size:10.5px;margin:5px 0 0 38px}
.footer .addr{position:absolute;left:428px;top:62px;display:flex;gap:14px;font-family:"Arimo",sans-serif;font-size:15px;font-weight:700;line-height:23px}
.footer .reach{position:absolute;left:795px;top:62px;font-family:"Arimo",sans-serif;font-size:15px;font-weight:700;line-height:30px}
.footer .reach div{display:flex;align-items:center;gap:14px}
.footer .rule{position:absolute;left:0;top:155px;width:1200px;height:1px;background:rgba(255,255,255,.55)}
.fcol{position:absolute;top:190px;font-family:"Arimo",sans-serif;font-size:13.5px;line-height:25px}
.fcol h4{font-size:18px;font-weight:700;margin-bottom:6px}
.fsocial{margin-top:18px;display:flex;gap:18px;font-weight:700}
.news input{display:none}
.news .box{margin-top:14px;width:290px;height:36px;display:flex}
.news .box span{flex:1;background:var(--white);color:#888;font-size:12px;padding:10px 8px}
.news .box b{width:40px;background:var(--teal);display:flex;align-items:center;justify-content:center}
.news small{display:block;font-size:10.5px;line-height:20px;margin-top:12px}
</style>
</head>
<body>

<div class="abs topbar">
  <div class="contact">
    <span><svg width="13" height="13" viewBox="0 0 24 24" fill="#fff"><path d="M6.6 10.8a15 15 0 0 0 6.6 6.6l2.2-2.2a1 1 0 0 1 1-.25 11.4 11.4 0 0 0 3.6.57 1 1 0 0 1 1 1V20a1 1 0 0 1-1 1A17 17 0 0 1 3 4a1 1 0 0 1 1-1h3.5a1 1 0 0 1 1 1c0 1.25.2 2.45.57 3.57a1 1 0 0 1-.25 1z"/></svg>08 9000 4172</span>
    <span><svg width="14" height="11" viewBox="0 0 24 18" fill="#fff"><path d="M0 0h24v2L12 10 0 2z"/><path d="M0 4l12 8 12-8v14H0z"/></svg>hello@brindlequay.com.au</span>
  </div>
  <div class="social"><span>f</span><span>in</span></div>
</div>

<header class="abs header">
  <div class="brand">
    <div class="name">brindle quay</div>
    <div class="tag">Proactive Business Accountants</div>
  </div>
  <div class="btn-consult">Book a Free Consultation</div>
  <nav class="nav">
    <span>Home</span><span>About Us</span><span class="active">Services</span><span>Testimonials</span><span>Articals</span><span>Events</span><span>Contact Us</span>
  </nav>
</header>

<section class="abs hero" role="img" aria-label="Photo of hands reviewing printed financial charts on a desk">
  <h1>SERVICES</h1>
</section>

<section class="abs intro">
  <p>Tax accounting is what most public practice accountants do. Management Accounting is very different – it's the accounting and reporting done in an organisation to help the owners/leaders make decisions. Both are done by accountants, but a different mind-set and skill-set is required for each.</p>
  <p>At Brindle Quay, we do both. We regularly see how timely decisions are made using Management Reports that would not have been made – and the positive differences those decisions make to businesses.</p>
  <p>Larger businesses generate Management Reports regularly (usually monthly) and can't imagine doing business without them. Smaller businesses often haven't discovered them yet and we've seen dramatic turn-arounds in business performance when they have.</p>
  <p>Hear what an engineering client, Dale, says about management reporting</p>
</section>

<div class="abs video" role="img" aria-label="Video still of a client and an adviser walking through a warehouse aisle">
  <svg class="play" width="58" height="58" viewBox="0 0 58 58"><circle cx="29" cy="29" r="29" fill="#fff"/><path d="M23 17l18 12-18 12z" fill="#222"/></svg>
</div>

<section class="abs quote">
  <p>This is what XXXX, a hospitality client says about management accounting:</p>
  <p>"We have worked with Brindle Quay for over 10 years now and really value the way they keep us focused on the numbers. They have shown us the KPI's we should be tracking in our most recent business venture, which gives us insights into areas that are going well and those that need work. We check in monthly to see how the business is performing against the forecast that we set together and it is great to have someone to be able to bounce ideas off."</p>
  <p class="cta-line"><span class="c">Contact Us</span> to find out more, or <span class="r">read on...</span></p>
</section>

<section class="abs band"></section>

<div class="acc" style="top:1951px">
  <div class="acc-head open">What's wrong with no Management Accounting?
    <svg width="26" height="26" viewBox="0 0 26 26"><circle cx="13" cy="13" r="13" fill="#fff"/><rect x="6" y="11" width="14" height="4" fill="#e15b62"/></svg>
  </div>
  <div class="acc-body">
    <div class="text">
      <p>Every SMB engages an accountant to do their tax accounting (it's the law). Once per year, their nominated tax accountant takes the data from the accounting system (typically Ledgerly or Tallybook) and prepares a report for the tax office so that the tax office can tell the business how much tax it should pay.</p>
      <p>The problem is, this reporting is done often 6 months after the end of a financial year, so the information is up to 18 months old. A lot can happen in one month let alone 18 - so this report is far too old to take quick action if things are not going well.</p>
      <p>We've seen businesses go spectacularly broke within a few months - generally our clients have been creditors of these businesses and we've seen up close what happened. They simply were not watching their finances - if they had been, the whole disaster could have been avoided.</p>
    </div>
    <div class="photo" role="img" aria-label="Photo of a handwritten ledger sheet full of figures"></div>
  </div>
</div>

<div class="acc" style="top:2383px"><div class="acc-head">Watching the bank account?<svg width="26" height="26" viewBox="0 0 26 26"><circle cx="13" cy="13" r="13" fill="#fff"/><path d="M11 6h4v5h5v4h-5v5h-4v-5H6v-4h5z" fill="#3aa9ee"/></svg></div></div>
<div class="acc" style="top:2450px"><div class="acc-head">Committed future expenses<svg width="26" height="26" viewBox="0 0 26 26"><circle cx="13" cy="13" r="13" fill="#fff"/><path d="M11 6h4v5h5v4h-5v5h-4v-5H6v-4h5z" fill="#3aa9ee"/></svg></div></div>
<div class="acc" style="top:2517px"><div class="acc-head">The Problem with the Profit &amp; Loss Report<svg width="26" height="26" viewBox="0 0 26 26"><circle cx="13" cy="13" r="13" fill="#fff"/><path d="M11 6h4v5h5v4h-5v5h-4v-5H6v-4h5z" fill="#3aa9ee"/></svg></div></div>
<div class="acc" style="top:2584px"><div class="acc-head">"Profit" isn't what you might think it is<svg width="26" height="26" viewBox="0 0 26 26"><circle cx="13" cy="13" r="13" fill="#fff"/><path d="M11 6h4v5h5v4h-5v5h-4v-5H6v-4h5z" fill="#3aa9ee"/></svg></div></div>
<div class="acc" style="top:2651px"><div class="acc-head">The Ups and Downs of Profit<svg width="26" height="26" viewBox="0 0 26 26"><circle cx="13" cy="13" r="13" fill="#fff"/><path d="M11 6h4v5h5v4h-5v5h-4v-5H6v-4h5z" fill="#3aa9ee"/></svg></div></div>
<div class="acc" style="top:2718px"><div class="acc-head">Management Accounts with Budget Forecasting is the Answer<svg width="26" height="26" viewBox="0 0 26 26"><circle cx="13" cy="13" r="13" fill="#fff"/><path d="M11 6h4v5h5v4h-5v5h-4v-5H6v-4h5z" fill="#3aa9ee"/></svg></div></div>
<div class="acc" style="top:2786px"><div class="acc-head">The Benefits of Management Reporting<svg width="26" height="26" viewBox="0 0 26 26"><circle cx="13" cy="13" r="13" fill="#fff"/><path d="M11 6h4v5h5v4h-5v5h-4v-5H6v-4h5z" fill="#3aa9ee"/></svg></div></div>
<div class="acc" style="top:2853px"><div class="acc-head">What can Brindle Quay do for you?<svg width="26" height="26" viewBox="0 0 26 26"><circle cx="13" cy="13" r="13" fill="#fff"/><path d="M11 6h4v5h5v4h-5v5h-4v-5H6v-4h5z" fill="#3aa9ee"/></svg></div></div>
<div class="acc" style="top:2920px"><div class="acc-head">The Brindle Quay Management Reporting package<svg width="26" height="26" viewBox="0 0 26 26"><circle cx="13" cy="13" r="13" fill="#fff"/><path d="M11 6h4v5h5v4h-5v5h-4v-5H6v-4h5z" fill="#3aa9ee"/></svg></div></div>

<h2 class="abs form-title">Contact us to discuss your needs</h2>
<div class="field" style="left:143px">Full name</div>
<div class="field" style="left:375px">Email Address</div>
<div class="field" style="left:607px">Phone Number</div>
<div class="field" style="left:838px">Subject</div>
<div class="field msg">Message</div>
<div class="abs submit">Submit</div>

<section class="abs cta">
  <p>Please contact us for more information and find out how<br>we can help you feel good about your future.</p>
  <div class="btn">Book A Free Consultation</div>
</section>

<footer class="abs footer">
  <div class="brand-f"><div class="name">brindle quay</div><div class="tag">Proactive Business Accountants</div></div>
  <div class="addr">
    <svg width="18" height="26" viewBox="0 0 18 26" fill="#fff"><path d="M9 0a9 9 0 0 1 9 9c0 7-9 17-9 17S0 16 0 9a9 9 0 0 1 9-9z"/><circle cx="9" cy="9" r="3.5" fill="#2e5375"/></svg>
    <div>Level 2, Ferncroft House<br>18 Wattlebird Lane, Westhaven WA 6999</div>
  </div>
  <div class="reach">
    <div><svg width="13" height="13" viewBox="0 0 24 24" fill="#fff"><path d="M6.6 10.8a15 15 0 0 0 6.6 6.6l2.2-2.2a1 1 0 0 1 1-.25 11.4 11.4 0 0 0 3.6.57 1 1 0 0 1 1 1V20a1 1 0 0 1-1 1A17 17 0 0 1 3 4a1 1 0 0 1 1-1h3.5a1 1 0 0 1 1 1c0 1.25.2 2.45.57 3.57a1 1 0 0 1-.25 1z"/></svg>08 9000 4172</div>
    <div><svg width="15" height="11" viewBox="0 0 24 18" fill="#fff"><path d="M0 0h24v2L12 10 0 2z"/><path d="M0 4l12 8 12-8v14H0z"/></svg>hello@brindlequay.com.au</div>
  </div>
  <div class="rule"></div>
  <div class="fcol" style="left:63px"><h4>Home</h4>About<br>People<br>Our Mission<br>Contact Us<div class="fsocial"><span>f</span><span>in</span></div></div>
  <div class="fcol" style="left:337px"><h4>Services</h4>Management Accounting<br>Tax Planning<br>Tax Compliance<br>Bookkeeping<br>Self Managed Super Funds<br>Business Education &amp; Seminars</div>
  <div class="fcol" style="left:612px"><h4>Link</h4>Testimonials<br>Events<br>Articles</div>
  <div class="fcol news" style="left:795px"><h4>Newsletter Sign up</h4>Receive our free regular knowledge bulletins
    <div class="box"><span>you@youremail.com.au</span><b><svg width="14" height="14" viewBox="0 0 24 24" fill="#fff"><path d="M2 11L22 2l-6 20-4-8z"/></svg></b></div>
    <small>© 2021. Brindle Quay. All Rights Reserved.<br>Website Design &amp; Hosting by larkspur web</small>
  </div>
</footer>

</body>
</html>
```